Brindlewick Solutions Ltd

I'd like to create a company letterhead for the attached logo in word format.

I'd like to emphasis the icon in large translucent state from the left corner and ensure that the letterhead colouring matches the colour palette of the current logo with a contrast so it's clear to see. I've attached a copy of our sister company page on the app for reference.

```html
<!DOCTYPE html>
<html lang="en">
<head>
<meta charset="utf-8">
<title>Brindlewick Solutions Ltd — Letterhead</title>
<link href="https://fonts.googleapis.com/css2?family=Arimo:wght@400&family=Mulish:wght@700&family=Open+Sans:wght@300&display=swap" rel="stylesheet">
<style>
  :root {
    --backdrop: #e2e2e2;
    --paper: #ffffff;
    --teal: #00bca7;
    --teal-faint: #eef8f8;
    --grey-rule: #9a9a9a;
    --ink: #555555;
    --ink-soft: #8e8e8e;
    --rule: #bdbdbd;
  }
  * { box-sizing: border-box; margin: 0; padding: 0; }
  html, body { width: 1200px; height: 1200px; overflow: hidden; background: var(--backdrop); }
  .letterhead {
    position: absolute; left: 233px; top: 81px;
    width: 734px; height: 1038px;
    background: var(--paper); overflow: hidden;
    font-family: "Arimo", Arial, sans-serif; color: var(--ink);
    box-shadow: 2px 2px 4px rgba(0,0,0,.25);
  }
  .watermark {
    position: absolute; left: -8px; top: 560px;
    width: 420px; height: 420px; border-radius: 50%;
    background: var(--teal-faint);
  }
  .footer-rule {
    position: absolute; left: 0; right: 0; bottom: 34px;
    height: 4px; background: var(--grey-rule);
  }
  .footer-band {
    position: absolute; left: 0; right: 0; bottom: 0;
    height: 26px; background: var(--teal);
  }
  .brand {
    position: absolute; left: 65px; top: 58px;
    display: flex; align-items: center; gap: 10px;
  }
  .brand-dot { width: 40px; height: 40px; border-radius: 50%; background: var(--teal); }
  .brand-name { font-size: 21px; color: var(--teal); }
  .contact {
    position: absolute; top: 53px; right: 65px;
    display: flex; font-size: 11.5px; line-height: 16.8px; color: var(--ink-soft);
  }
  .contact-address { font-style: normal; text-align: right; padding-right: 10px; border-right: 1px solid var(--rule); }
  .contact-lines { padding-left: 10px; list-style: none; }
  .contact-lines li { display: flex; align-items: center; gap: 7px; }
  .contact-lines svg { width: 10px; height: 10px; fill: var(--teal); }
  .salutation {
    position: absolute; left: 67px; top: 319px;
    font-family: "Mulish", sans-serif; font-weight: 700; font-size: 17px; color: var(--ink);
  }
  .letter-body {
    position: absolute; left: 65px; top: 366px; width: 604px;
    font-size: 12.3px; line-height: 15.2px;
  }
  .letter-body p { margin-bottom: 13px; }
  .closing {
    position: absolute; left: 67px; top: 678px;
    font-family: "Mulish", sans-serif; font-weight: 700; font-size: 9.5px;
  }
  .signature {
    position: absolute; left: 84px; top: 725px;
    font-family: "Open Sans", sans-serif; font-weight: 300; font-size: 17px;
    letter-spacing: -1px; color: var(--ink);
  }
</style>
</head>
<body>
<main class="letterhead">
  <div class="watermark" aria-hidden="true"></div>
  <div class="footer-rule" aria-hidden="true"></div>
  <div class="footer-band" aria-hidden="true"></div>

  <header>
    <div class="brand">
      <span class="brand-dot"></span>
      <span class="brand-name">Brindlewick Solutions Ltd</span>
    </div>
    <div class="contact">
      <address class="contact-address">Your address<br>city<br>state, ZIP 0000</address>
      <ul class="contact-lines">
        <li><svg viewBox="0 0 24 24"><path d="M6.6 10.8a15 15 0 0 0 6.6 6.6l2.2-2.2a1 1 0 0 1 1-.25 11.4 11.4 0 0 0 3.6.57 1 1 0 0 1 1 1V20a1 1 0 0 1-1 1A17 17 0 0 1 3 4a1 1 0 0 1 1-1h3.5a1 1 0 0 1 1 1c0 1.25.2 2.45.57 3.57a1 1 0 0 1-.25 1z"/></svg>555-014-2100</li>
        <li><svg viewBox="0 0 24 24"><path d="M2 5h20v14H2z M2 5l10 8 10-8" stroke="#fff" stroke-width="1.5"/></svg>youremail@mailbox.com</li>
        <li><svg viewBox="0 0 24 24"><circle cx="12" cy="12" r="10"/><path d="M2 12h20M12 2c3 3 3 17 0 20M12 2c-3 3-3 17 0 20" stroke="#fff" stroke-width="1.4" fill="none"/></svg>www.brindlewick.com</li>
      </ul>
    </div>
  </header>

  <h1 class="salutation">Dear Mr. Harlow,</h1>

  <section class="letter-body">
    <p>Lorem ipsum dolor sit amet, consectetuer adipiscing elit, sed diam nonmmy nibh euismod tincidunt ut laor eet dolore magna aliquam erat volutpat. Ut wisi enim ad minim veniam, quis nostrud exerci tationmcorper suscipit lobortis nisl ut aliquip ex ea commodo consequat. Duis autem vel eum iriure dolor in hendrerit in vulputate velit esse molestie consequat, vel illum dolore eu feugiat</p>
    <p>Rorem ipsum dolor sit amet, consectetuer adipiscing elit, sed diam nonmmy nibh euismod tincidunt ut laor eet dolore magna aliquam erat volutpat. Ut wisi enim ad minim veniam, quis nostrud exerci tationmcorper suscipit lobortis nisl ut aliquip ex ea commodo consequat. Duis autem vel eum iriure dolor in hendrerit in vulputate velit esse molest</p>
    <p>Dorem ipsum dolor sit amet, consectetuer adipiscing elit, sed diam nonmmy nibh euismod tincidunt ut laor eet dolore magna aliquam erat volutpat. Ut wisi enim ad minim veniam, quis nostrud exerci tationmcorper suscipit lobortis nisl ut aliquip ex ea commodo consequat. Duis autem vel eum iriure dolor in hendrerit in suscipit lobortis nisl ut aliquip ex ea commodo consequat. Duis autem vel eum iriure dolor in hendrerit in vulputate velit esse molestie consequat, vel illum</p>
    <p>Sorem ipsum dolor sit amet, consectetuer adipiscing elit, sed diam nonmmy nibh euismod tincidunt ut laor eet dolore magna aliquam erat volutpat. Ut wisi enim ad minim veniam, quis nostrud exerci tationmcorper suscipit lobortis nisl ut aliquip ex ea commodo consequat. Duis autem vel eum iriure dolor in</p>
  </section>

  <p class="closing">Sincerely,</p>
  <p class="signature">Marla Quintrell</p>
</main>
</body>
</html>
```